Ward Compass Business Card Design*

We need a business card design for our company Ward Compass. Our company is specialized in providing online consulting services regarding medical institutions, hospitals and doctors. We work with patients worldwide looking to choose between healthcare providers. We have a website you may use as a reference, where we list doctors and clinics worldwide. So we target Medical providers as well as patients worldwide.
Target Market(s)
Medical Providers and patients around the world
Industry/Entity Type
Medical
Contact Information for Business Card
Salwa Kettani
CEO
+90 612 348 2175
info@wardcompass.example
www.wardcompass.example
14 Annakhil 7 H.R.B. Rabat, Morocco
Requirements
Must have
- Company logo/name on one full side, personal info and smaller logo and company name on the other side.
Nice to have
- Smart and elegant design

```html
<!DOCTYPE html>
<html lang="en">
<head>
<meta charset="utf-8">
<title>Ward Compass – Business Card</title>
<link rel="stylesheet" href="https://fonts.googleapis.com/css2?family=Mulish:wght@400;600;800&display=swap">
<style>
  :root {
    --navy: #1a4574;
    --paper: #f3f3f5;
    --ink: #2b3240;
    --muted: #4a4f59;
    --grey-mark: #8b8b8e;
    --rule: #9a9ca3;
    --backdrop: #e4e2de;
  }
  * { margin: 0; padding: 0; box-sizing: border-box; }
  html, body { width: 900px; height: 1200px; overflow: hidden; }
  body {
    position: relative;
    background: var(--backdrop);
    font-family: "Mulish", sans-serif;
  }
  .card {
    position: absolute;
    left: 77px;
    width: 746px;
    height: 436px;
  }
  .card-front { top: 134px; background: var(--navy); }
  .card-back { top: 637px; background: var(--paper); }

  .brand {
    position: absolute;
    display: flex;
    align-items: center;
  }
  .brand-dot { border-radius: 50%; flex: none; }
  .brand-name { font-weight: 600; letter-spacing: 0.02em; white-space: nowrap; }

  .card-front .brand { left: 135px; top: 173px; gap: 26px; }
  .card-front .brand-dot { width: 100px; height: 100px; background: var(--grey-mark); }
  .card-front .brand-name { color: #fff; font-size: 46px; }

  .website {
    position: absolute;
    left: 0; right: 0; top: 423px;
    text-align: center;
    color: #fff;
    font-size: 16px;
    letter-spacing: 0.02em;
  }
  .card-front .website { top: 391px; }

  .card-back .brand { left: 424px; top: 58px; gap: 14px; }
  .card-back .brand-dot { width: 62px; height: 62px; background: var(--navy); }
  .card-back .brand-name { color: var(--navy); font-size: 26px; }

  .divider-vertical {
    position: absolute;
    left: 381px; top: 152px;
    width: 1px; height: 131px;
    background: var(--ink);
  }

  .person {
    position: absolute;
    left: 35px; top: 260px;
    width: 228px;
    text-align: center;
  }
  .person-name { font-size: 26px; color: var(--ink); white-space: nowrap; letter-spacing: 0.01em; }
  .person-name .given { font-weight: 800; color: var(--navy); }
  .person-name .family { font-weight: 400; }
  .person-role { font-size: 18px; color: var(--muted); margin-top: 2px; }

  .divider-horizontal {
    position: absolute;
    left: 35px; top: 329px;
    width: 239px; height: 1px;
    background: var(--rule);
  }

  .contact-list {
    position: absolute;
    left: 54px; top: 360px;
    list-style: none;
  }
  .contact-list li {
    display: flex;
    align-items: center;
    gap: 11px;
    height: 26px;
    font-size: 18px;
    color: var(--ink);
  }
  .contact-icon { width: 18px; height: 18px; flex: none; }
</style>
</head>
<body>
  <section class="card card-front" aria-label="Card front">
    <div class="brand">
      <span class="brand-dot" aria-hidden="true"></span>
      <span class="brand-name">WARD COMPASS</span>
    </div>
    <p class="website">www.wardcompass.example</p>
  </section>

  <section class="card card-back" aria-label="Card back">
    <div class="brand">
      <span class="brand-dot" aria-hidden="true"></span>
      <span class="brand-name">WARD COMPASS</span>
    </div>

    <span class="divider-vertical" aria-hidden="true"></span>

    <div class="person">
      <p class="person-name"><span class="given">SALWA</span> <span class="family">KETTANI</span></p>
      <p class="person-role">CEO</p>
    </div>

    <span class="divider-horizontal" aria-hidden="true"></span>

    <ul class="contact-list">
      <li>
        <svg class="contact-icon" viewBox="0 0 18 18" aria-hidden="true">
          <circle cx="9" cy="9" r="9" fill="#1a4574"/>
          <path d="M6.2 4.6l1.4 1.9-.9 1.1c.5 1.2 1.5 2.2 2.7 2.7l1.1-.9 1.9 1.4-.7 1.6c-3.4-.2-6.1-2.9-6.3-6.3z" fill="#fff"/>
        </svg>
        <span>+90 612 348 2175</span>
      </li>
      <li>
        <svg class="contact-icon" viewBox="0 0 18 18" aria-hidden="true">
          <circle cx="9" cy="9" r="9" fill="#1a4574"/>
          <rect x="5" y="6" width="8" height="6" fill="#fff"/>
          <path d="M5 6l4 3.2L13 6" fill="none" stroke="#1a4574" stroke-width="0.9"/>
        </svg>
        <span>info@wardcompass.example</span>
      </li>
    </ul>
  </section>
</body>
</html>
```